Upscale business cards needed for Board of Directors

We need professional business cards created for members of our family business Board of Directors. We would like these relatively simple and straightforward, but also with a unique element to set them apart. Probably stick with neutral and simple colors - white, grey etc. We need space for the traditional elements, including name, title, address, email/phone number. And we will be creating several from this template so it needs to be template that is easy to switch information in and out of.
Business
See description

```html
<!DOCTYPE html>
<html lang="en">
<head>
<meta charset="utf-8">
<title>Harborline Holdings – Business Card</title>
<link rel="stylesheet" href="https://fonts.googleapis.com/css2?family=Arimo:wght@400;700&display=swap">
<style>
  :root {
    --backdrop: #3a302b;
    --card: #141414;
    --card-edge: #1d1d1d;
    --white: #f2f2f2;
    --silver: #b9b9b9;
    --gold: #b59a6a;
    --divider: #5a5a5a;
  }
  * { margin: 0; padding: 0; box-sizing: border-box; }
  html, body {
    width: 1200px; height: 864px; overflow: hidden;
    background: var(--backdrop);
    font-family: "Arimo", Arial, sans-serif;
  }
  .stage { position: relative; width: 1200px; height: 864px; }
  .card {
    position: absolute;
    width: 600px; height: 343px;
    background: var(--card);
    border: 1px solid var(--card-edge);
    box-shadow: 0 18px 40px rgba(0,0,0,.45);
  }
  .card--back { left: 70px; top: 70px; }
  .card--front { left: 530px; top: 450px; }

  .wordmark {
    position: absolute;
    text-align: center;
    font-weight: 700;
    text-transform: uppercase;
    line-height: 1;
  }
  .wordmark__main { display: block; font-size: 38px; letter-spacing: 1px; }
  .wordmark__sub { display: block; font-size: 19px; letter-spacing: 8px; margin-top: 6px; }
  .card--back .wordmark { right: 50px; bottom: 58px; color: var(--silver); }
  .card--front .wordmark { left: 34px; top: 128px; color: var(--white); }

  .divider {
    position: absolute; left: 330px; top: 80px;
    width: 1px; height: 190px;
    background: linear-gradient(to bottom, transparent, var(--divider) 20%, var(--divider) 80%, transparent);
  }
  .details { position: absolute; left: 352px; top: 88px; color: var(--white); }
  .details__name { font-size: 19px; color: var(--gold); letter-spacing: .5px; }
  .details__title { font-size: 15px; margin-top: 4px; }
  .details__address { font-size: 13px; line-height: 18px; margin-top: 14px; }
  .contact { list-style: none; margin-top: 10px; font-size: 13px; }
  .contact__item { display: flex; align-items: center; gap: 8px; height: 22px; }
  .contact__icon { width: 14px; height: 14px; flex: none; }
</style>
</head>
<body>
<main class="stage">
  <section class="card card--back" aria-label="Card back">
    <div class="wordmark">
      <span class="wordmark__main">Harborline</span>
      <span class="wordmark__sub">Holdings</span>
    </div>
  </section>

  <section class="card card--front" aria-label="Card front">
    <div class="wordmark">
      <span class="wordmark__main">Harborline</span>
      <span class="wordmark__sub">Holdings</span>
    </div>
    <div class="divider"></div>
    <div class="details">
      <p class="details__name">Daniel Marsh</p>
      <p class="details__title">President</p>
      <p class="details__address">2170 Linden Grove Road<br>Oak Harbor, NY 11420</p>
      <ul class="contact">
        <li class="contact__item">
          <svg class="contact__icon" viewBox="0 0 14 14" aria-hidden="true"><circle cx="7" cy="7" r="7" fill="var(--gold)"/><path d="M4.5 3.5h1.6l.7 2-1 .8a5 5 0 0 0 2.3 2.3l.8-1 2 .7v1.6c0 .4-.3.6-.7.6A6.5 6.5 0 0 1 3.9 4.2c0-.4.2-.7.6-.7z" fill="var(--card)"/></svg>
          555 0142 7788
        </li>
        <li class="contact__item">
          <svg class="contact__icon" viewBox="0 0 14 14" aria-hidden="true"><circle cx="7" cy="7" r="7" fill="var(--gold)"/><rect x="3.3" y="4.5" width="7.4" height="5" fill="var(--card)"/><path d="M3.3 4.5 7 7.4l3.7-2.9" stroke="var(--gold)" stroke-width=".8" fill="none"/></svg>
          daniel@harborline.com
        </li>
        <li class="contact__item">
          <svg class="contact__icon" viewBox="0 0 14 14" aria-hidden="true"><circle cx="7" cy="7" r="7" fill="var(--gold)"/><circle cx="7" cy="7" r="3.6" fill="none" stroke="var(--card)" stroke-width=".9"/><path d="M3.4 7h7.2M7 3.4c-1.6 2.2-1.6 5 0 7.2M7 3.4c1.6 2.2 1.6 5 0 7.2" stroke="var(--card)" stroke-width=".8" fill="none"/></svg>
          www.harborline.com
        </li>
      </ul>
    </div>
  </section>
</main>
</body>
</html>
```